Business Card for Beach theme sports bar called MORVIN

I need a business card designed for our employees, front and back. This will be used by the employees of two business locations to hand out to customers. I've attached the previous business cards we used at one time for a Dantells (it is now Morvin). Looking for a fresh new card that is elegant but has character.

Target Market(s)

30-60, middle class

Contact Information for Business Card

We are a beach bar and sports bar. I am looking for an elegant business card with the front to have the MORVIN logo. Then on the back I need it to allow a space for employees to write their names and for them to write in their schedule. I have attached our old cards with our old name Dantells so you can pull everything we need on the cards. one thing is missing is we have another location at 2615 W Calder Ridge Rd with a number of 702-418-9053. Since we will use it for both locations it should allow the employee to circle or check mark the bar which they work at.

Font styles to use
Sans Serif

Requirements
Must have
• We are looking for some fresh ideas for the business card. Something that will really stick out to customers when the staff hands them out. Creativity will be looked at positively, but we still want it to look upscale and fun.

```html
<!DOCTYPE html>
<html lang="en">
<head>
<meta charset="utf-8">
<title>Morvin – Employee Business Card</title>
<link rel="stylesheet" href="https://fonts.googleapis.com/css2?family=Oswald:wght@300;400;500;600;700&display=swap">
<style>
  :root {
    --page-bg: #e4e3e1;
    --card-dark: #3a3431;
    --card-gold: #d8ae3b;
    --ink-dark: #2f2926;
    --ink-light: #ffffff;
    --accent-gold: #d8ae3b;
    --ribbon: #ffffff;
    --ribbon-shade: #d9d6cf;
  }
  * { box-sizing: border-box; margin: 0; padding: 0; }
  html, body { width: 1200px; height: 900px; overflow: hidden; }
  body {
    background: var(--page-bg);
    font-family: "Oswald", sans-serif;
    display: flex;
    flex-direction: column;
    align-items: center;
    justify-content: center;
    gap: 40px;
  }
  .card {
    position: relative;
    width: 660px;
    height: 377px;
    overflow: hidden;
    box-shadow: 0 6px 18px rgba(0,0,0,0.18);
  }

  /* ---------- Front ---------- */
  .card--front { background: var(--card-dark); color: var(--ink-light); }
  .front__tagline {
    position: absolute; left: 200px; top: 30px;
    line-height: 1;
  }
  .front__tagline-main {
    display: block; color: var(--accent-gold);
    font-weight: 600; font-size: 22px; letter-spacing: 0.5px;
  }
  .front__tagline-group {
    display: block; margin-top: 4px;
    font-weight: 400; font-size: 11px; letter-spacing: 3.2px;
  }
  .front__brand {
    position: absolute; left: 0; right: 0; top: 78px;
    display: flex; align-items: center; justify-content: center; gap: 22px;
  }
  .front__brand-mark {
    width: 34px; height: 34px; border-radius: 50%;
    background: var(--ink-light);
  }
  .front__brand-name {
    font-weight: 700; font-size: 148px; line-height: 1;
    color: var(--ink-light); letter-spacing: 2px;
  }
  .front__offer {
    position: absolute; right: 38px; bottom: 26px;
    text-align: right; line-height: 0.9;
  }
  .front__offer-amount {
    display: block; color: var(--accent-gold);
    font-weight: 700; font-size: 92px;
  }
  .front__offer-label {
    display: block; font-weight: 600; font-size: 34px; letter-spacing: 0.5px;
  }

  /* ---------- Back ---------- */
  .card--back { background: var(--card-gold); color: var(--ink-dark); }
  .location { position: absolute; line-height: 1.2; }
  .location--primary { left: 36px; top: 30px; }
  .location--secondary { right: 36px; top: 178px; text-align: left; }
  .location__check {
    display: flex; gap: 18px; margin-bottom: 6px; padding-left: 6px;
  }
  .location__check span {
    display: block; width: 2px; height: 14px; background: var(--ink-dark);
  }
  .location__street, .location__city { font-size: 15px; font-weight: 400; }
  .location__phone { font-size: 30px; font-weight: 600; letter-spacing: 0.5px; margin-top: 2px; }

  .back__brand {
    position: absolute; left: 240px; top: 26px; width: 180px;
    display: flex; align-items: center; justify-content: center; gap: 10px;
  }
  .back__brand-mark { width: 14px; height: 14px; border-radius: 50%; background: var(--ink-dark); }
  .back__brand-name { font-weight: 700; font-size: 52px; line-height: 1; }
  .back__role {
    position: absolute; left: 240px; top: 92px; width: 180px;
    text-align: center; font-size: 20px; font-weight: 400; letter-spacing: 1px;
  }
  .name-ribbon { position: absolute; left: 200px; top: 122px; width: 260px; height: 64px; }

  .schedule {
    position: absolute; left: 196px; top: 198px; width: 250px;
    display: grid; grid-template-columns: repeat(7, 1fr);
    font-size: 17px; font-weight: 500; text-align: center;
  }
  .schedule__day {
    border-right: 2px solid var(--ink-dark); line-height: 1.3;
  }
  .schedule__day:last-child { border-right: none; }
  .schedule__slot {
    height: 22px; border-right: 2px solid var(--ink-dark);
  }
  .schedule__slot:nth-child(7n) { border-right: none; }

  .fine-print {
    position: absolute; left: 36px; bottom: 26px; width: 470px;
    font-size: 13px; font-weight: 400; line-height: 1.4;
  }
</style>
</head>
<body>

  <section class="card card--front" aria-label="Card front">
    <div class="front__tagline">
      <span class="front__tagline-main">A GAMERS BAR</span>
      <span class="front__tagline-group">MORVIN TAVERN GROUP</span>
    </div>
    <div class="front__brand">
      <span class="front__brand-name">Morvin</span>
      <span class="front__brand-mark"></span>
    </div>
    <div class="front__offer">
      <span class="front__offer-amount">$20</span>
      <span class="front__offer-label">MATCH PLAY</span>
    </div>
  </section>

  <section class="card card--back" aria-label="Card back">
    <div class="location location--primary">
      <div class="location__check"><span></span><span></span></div>
      <p class="location__street">3180 W Harlow Crest Rd</p>
      <p class="location__city">Las Vegas, NV 89146</p>
      <p class="location__phone">702-531-6274</p>
    </div>

    <div class="back__brand">
      <span class="back__brand-name">Morvin</span>
      <span class="back__brand-mark"></span>
    </div>
    <p class="back__role">BARTENDER</p>

    <svg class="name-ribbon" viewBox="0 0 260 64" aria-label="Space for employee name">
      <polygon points="0,22 30,22 30,56 0,56 12,39" fill="var(--ribbon-shade)"/>
      <polygon points="260,22 230,22 230,56 260,56 248,39" fill="var(--ribbon-shade)"/>
      <rect x="22" y="8" width="216" height="42" fill="var(--ribbon)"/>
    </svg>

    <div class="schedule" aria-label="Weekly schedule">
      <span class="schedule__day">M</span>
      <span class="schedule__day">T</span>
      <span class="schedule__day">W</span>
      <span class="schedule__day">Th</span>
      <span class="schedule__day">F</span>
      <span class="schedule__day">Sa</span>
      <span class="schedule__day">Su</span>
      <span class="schedule__slot"></span>
      <span class="schedule__slot"></span>
      <span class="schedule__slot"></span>
      <span class="schedule__slot"></span>
      <span class="schedule__slot"></span>
      <span class="schedule__slot"></span>
      <span class="schedule__slot"></span>
    </div>

    <div class="location location--secondary">
      <div class="location__check"><span></span><span></span></div>
      <p class="location__street">2615 W Calder Ridge Rd</p>
      <p class="location__city">Las Vegas, NV 89146</p>
      <p class="location__phone">702-418-9053</p>
    </div>

    <div class="fine-print">
      <p>Match play for new slot members, must play total 100 coin. Please see bartender for details.</p>
      <p>Management reserves all rights.</p>
      <p>cs@morvinbar.com</p>
    </div>
  </section>

</body>
</html>
```